Business Card Design For A Cajun Seafood Restaurant

We are opening a cajun seafood restaurant in a week. We mainly serve cajun seafood which is orginally from Louisiana. We want design on both sides of a business card. I have menu on the website. You can go to www.reednkettle.example to check out our menu.

Restaurant name: Reed N' Kettle
Phone: +1 (555) 304-7712
Address: 48206 Ludlow Row, #7, Bexmoor Flats, Ca90000
Email: reednkettle@mailbox.example
Website: www.reednkettle.example

Maybe add social media icons (facebook, instagram) if looks nice on the business card.
facebook.com/reednkettle
instagram.com/reednkettle or @reednkettle

Attached is the logo and other business card samples that I like.

```html
<!DOCTYPE html>
<html lang="en">
<head>
<meta charset="utf-8">
<title>Reed N' Kettle — Business Card</title>
<link rel="stylesheet" href="https://fonts.googleapis.com/css2?family=Roboto:wght@400;500;700&display=swap">
<style>
  :root {
    --bg: #1c1c1e;
    --card-light: #ffffff;
    --card-dark: #2e2e30;
    --orange: #f06a12;
    --ink: #2a2a2a;
    --muted: #5a5a5a;
    --rule: #3a3a3a;
    --art-warm: #e8641c;
    --art-light: #f2a531;
  }
  * { box-sizing: border-box; margin: 0; padding: 0; }
  html, body { width: 1200px; height: 950px; overflow: hidden; background: var(--bg); }
  body { font-family: "Roboto", Arial, sans-serif; position: relative; }

  .card {
    position: absolute;
    left: 232px;
    width: 736px;
    height: 420px;
    border-radius: 4px;
    overflow: hidden;
  }
  .card--front { top: 40px; background: var(--card-light); border-bottom: 10px solid var(--orange); }
  .card--back  { top: 490px; background: var(--card-dark); }

  /* Front */
  .brand {
    position: absolute; top: 52px; right: 56px;
    display: flex; align-items: center; gap: 14px;
  }
  .brand__dot { width: 22px; height: 22px; border-radius: 50%; background: var(--orange); }
  .brand__name { font-size: 34px; font-weight: 700; color: var(--orange); letter-spacing: 0.5px; }

  .divider {
    position: absolute; top: 150px; left: 330px; right: 56px;
    height: 1px; background: var(--rule);
  }
  .address {
    position: absolute; top: 172px; right: 56px;
    text-align: right; font-size: 17px; line-height: 1.45; color: var(--muted);
    font-style: normal;
  }

  .person { position: absolute; left: 56px; top: 232px; }
  .person__name { font-size: 26px; font-weight: 500; color: var(--orange); }
  .person__title { font-size: 17px; color: var(--ink); margin-top: 2px; }

  .contacts { list-style: none; margin-top: 18px; }
  .contacts li {
    display: flex; align-items: center; gap: 10px;
    font-size: 15px; color: var(--muted); line-height: 1.7;
  }
  .contacts svg { width: 15px; height: 15px; flex: none; }

  /* Back */
  .mascot {
    position: absolute; left: 268px; top: 70px;
    width: 280px; height: 240px;
    border-radius: 16px;
    background: linear-gradient(135deg, var(--art-warm), var(--art-light));
    opacity: 0.9;
  }
  .social {
    position: absolute; left: 56px; bottom: 44px;
    display: flex; align-items: center; gap: 22px;
    font-size: 16px; color: #e6e6e6;
  }
  .social__item { display: flex; align-items: center; gap: 8px; }
  .social__mark { width: 14px; height: 14px; border-radius: 50%; background: var(--orange); }
</style>
</head>
<body>

  <section class="card card--front" aria-label="Card front">
    <div class="brand">
      <span class="brand__dot"></span>
      <span class="brand__name">Reed N' Kettle</span>
    </div>
    <div class="divider"></div>
    <address class="address">
      48206 Ludlow Row, #7<br>
      Bexmoor Flats, Ca90000
    </address>

    <div class="person">
      <p class="person__name">Marcus Vane</p>
      <p class="person__title">President</p>
      <ul class="contacts">
        <li>
          <svg viewBox="0 0 16 16" aria-hidden="true"><path fill="#f06a12" d="M3 1h3l1 4-2 1c1 2 3 4 5 5l1-2 4 1v3c0 1-1 2-2 2C7 15 1 9 1 3c0-1 1-2 2-2z"/></svg>
          +1 (555) 304-7712
        </li>
        <li>
          <svg viewBox="0 0 16 16" aria-hidden="true"><rect x="1" y="3" width="14" height="10" rx="1" fill="#f06a12"/><path d="M1.5 4l6.5 5 6.5-5" fill="none" stroke="#fff" stroke-width="1.3"/></svg>
          reednkettle@mailbox.example
        </li>
        <li>
          <svg viewBox="0 0 16 16" aria-hidden="true"><circle cx="8" cy="8" r="7" fill="#f06a12"/><path d="M1 8h14M8 1c3 3 3 11 0 14M8 1c-3 3-3 11 0 14" fill="none" stroke="#fff" stroke-width="1"/></svg>
          www.reednkettle.example
        </li>
      </ul>
    </div>
  </section>

  <section class="card card--back" aria-label="Card back">
    <div class="mascot" role="img" aria-label="Illustration of the restaurant mascot holding an ear of corn"></div>
    <div class="social">
      <span class="social__item"><span class="social__mark"></span>reednkettle</span>
      <span class="social__item"><span class="social__mark"></span>@reednkettle</span>
    </div>
  </section>

</body>
</html>
```